Website Development for vaultmerrow.com.au

Build a new Wordpress/Responsive website for vaultmerrow.com.au

Target Market(s)

Compliance Managers, Risk Managers, Information Security and Cyber Security Professionals, Chief Data/Digital Officers, Chief Operating/Financial Officers, Business Continuity Professionals, Disaster Recovery Planners, Small Business Owners, Local/Federal Government entities

Industry/Entity Type

Data Service

Coding

Coded - Design and coding required

Number of Pages Required

5+ page

Font styles to use
Sans Serif

Colors

Designer to choose colors to be used in the design.

Requirements
Must have
• 1. Site Structure: Home Page plus the following chapter-pages for a) Services b) About c) Resources d) Blog e) Contact Us
• 2. Prefer site to built on wordpress and we can purchase a theme if needed (we currently use Kelp9 for other sites)
• 3. Blog needs to be wordpress based
• 4. We will host the site ourselves on our own servers
• 5. Responsive Design
Nice to have
• 1. Livechat capability/interface
• 2. Capability for marketing automation integration (such as hubspot, marketo, infusionsoft etc)
• 3. Capability for CRM integration (Salesforce)

```html
<!DOCTYPE html>
<html lang="en">
<head>
<meta charset="utf-8">
<title>Vaultmerrow</title>
<link href="https://fonts.googleapis.com/css2?family=Lato:wght@400;700;900&display=swap" rel="stylesheet">
<style>
:root{
  --red:#e3141b;
  --ink:#1b1b1b;
  --text:#4a4a4a;
  --muted:#777;
  --line:#e2e2e2;
  --pale:#eeeeee;
  --footer:#111111;
  --grey-btn:#4d4d4d;
}
*{margin:0;padding:0;box-sizing:border-box}
html,body{width:1200px;height:4737px;overflow:hidden;background:#fff}
body{font-family:'Lato',sans-serif;color:var(--text);position:relative}
.abs{position:absolute}
.btn{position:absolute;display:flex;align-items:center;justify-content:center;height:40px;border-radius:20px;background:var(--red);color:#fff;font-weight:700;font-size:13px;letter-spacing:.5px;text-transform:uppercase;white-space:nowrap}
.brand{position:absolute;display:flex;align-items:center;gap:12px;color:var(--red);font-weight:900;white-space:nowrap}
.brand-mark{background:var(--red);border-radius:50%;flex:none}

/* header */
.site-header{position:absolute;left:0;top:0;width:1200px;height:105px;background:#fff}
.site-header .brand{left:76px;top:30px;font-size:30px;line-height:40px}
.site-header .brand-mark{width:40px;height:40px}
.main-nav{position:absolute;right:76px;top:44px;display:flex;gap:36px;font-size:14px;font-weight:700;color:var(--ink)}
.main-nav .active{color:var(--red)}

/* hero */
.hero{position:absolute;left:0;top:105px;width:1200px;height:640px;overflow:hidden}
.hero-photo{position:absolute;inset:0;background:linear-gradient(115deg,#22303f 0%,#3d5066 40%,#1d2633 75%,#2d3a48 100%)}
.hero-title{position:absolute;left:0;width:1200px;top:185px;text-align:center;color:#fff;font-weight:900;font-size:88px;line-height:100px;letter-spacing:1px;white-space:nowrap}
.hero-sub{position:absolute;left:0;width:1200px;top:295px;text-align:center;color:#fff;font-weight:900;font-size:26px;line-height:34px;white-space:nowrap}
.hero .btn{left:523px;top:365px;width:177px}
.dots{position:absolute;left:568px;top:543px;display:flex;gap:10px}
.dots span{width:12px;height:12px;border-radius:50%;background:#fff;opacity:.6}
.dots span:first-child{opacity:1;background:var(--red)}

/* welcome */
.welcome{position:absolute;left:0;top:745px;width:1200px;height:376px;overflow:hidden}
.welcome .brand{left:76px;top:150px;font-size:50px;line-height:70px}
.welcome .brand-mark{width:64px;height:64px}
.section-title{font-weight:900;color:var(--ink);font-size:28px;line-height:36px;text-transform:uppercase}
.welcome h2{position:absolute;left:524px;top:42px}
.welcome .welcome-text{position:absolute;left:524px;top:93px;width:580px;font-size:15px;line-height:28px}
.welcome .btn{left:524px;top:250px;width:180px}

/* bands */
.band{position:absolute;left:0;width:1200px;height:445px;overflow:hidden}
.band-photo{position:absolute;inset:0}
.band-text{position:absolute;left:0;width:1200px;top:180px;text-align:center;color:#fff;font-weight:900;font-size:29px;line-height:44px}

/* services */
.services h2{position:absolute;left:0;width:1200px;top:1628px;text-align:center}
.services .intro{position:absolute;left:120px;width:960px;top:1682px;text-align:center;font-size:15px;line-height:28px}
.service{position:absolute;width:330px;text-align:center}
.service svg{display:block;margin:0 auto}
.service h3{color:var(--red);font-size:18px;font-weight:900;margin-top:20px;text-transform:uppercase}
.service p{font-size:14px;line-height:24px;margin:8px auto 0;width:260px}
.vline{position:absolute;width:1px;background:var(--line)}
.hline{position:absolute;height:1px;background:var(--line)}
.services .btn{left:492px;top:2500px;width:216px;background:var(--grey-btn)}

/* resources */
.res-photo{position:absolute;left:76px;top:3133px;width:512px;height:366px;background:linear-gradient(135deg,#5d6b7b 0%,#c7ccd3 55%,#e6e2dc 100%)}
.resources h2{position:absolute;left:613px;top:3125px}
.resources p{position:absolute;left:613px;width:512px;font-size:15px;line-height:28px}
.resources .btn{left:613px;top:3458px;width:180px}

/* blog */
.blog-bg{position:absolute;left:0;top:3578px;width:1200px;height:690px;background:var(--pale)}
.blog h2{position:absolute;left:0;width:1200px;top:3643px;text-align:center}
.post{position:absolute;top:3714px;width:512px}
.post-photo{height:259px}
.post h3{margin-top:24px;font-size:18px;font-weight:900;color:var(--ink);text-transform:uppercase}
.post p{margin-top:10px;font-size:14px;line-height:22px}
.post p span{color:var(--red)}
.blog .btn{left:510px;top:4161px;width:180px}

/* footer */
.site-footer{position:absolute;left:0;top:4257px;width:1200px;height:480px;background:var(--footer);color:#ddd}
.fcol{position:absolute;top:115px;font-size:13px;line-height:28px}
.fcol h4{color:#fff;font-size:15px;font-weight:900;margin-bottom:4px;text-transform:uppercase}
.fcol .row{display:flex;align-items:center;gap:14px}
.email-field{width:240px;height:42px;border:1px solid #fff;border-radius:21px;padding-left:20px;display:flex;align-items:center;font-size:13px;margin-top:8px}
.site-footer .btn{height:36px;font-size:12px}
.socials{display:flex;gap:14px;margin-top:8px}
.socials span{width:18px;height:18px;border-radius:50%;background:#ddd}
.chat{position:absolute;left:884px;top:300px;width:180px;height:44px;border:1px solid #fff;border-radius:22px;display:flex;align-items:center;justify-content:center;gap:10px;color:#fff;font-size:13px;font-weight:700}
.copyright{position:absolute;left:0;width:1200px;top:392px;border-top:1px solid #333;padding-top:38px;text-align:center;font-size:12px;color:#bbb}
</style>
</head>
<body>

<header class="site-header">
  <div class="brand"><span class="brand-mark"></span>Vaultmerrow</div>
  <nav class="main-nav">
    <span class="active">HOME</span><span>ABOUT US</span><span>SERVICES</span><span>RESOURCES</span><span>BLOG</span><span>CONTACT US</span>
  </nav>
</header>

<section class="hero">
  <div class="hero-photo" role="img" aria-label="Photo of two professionals reviewing data in a server room"></div>
  <h1 class="hero-title">VAULTMERROW</h1>
  <p class="hero-sub">MAURIS NEC QUAM DICTUM CONVALLIS EROS ID TEMPOR...</p>
  <span class="btn">Read More</span>
  <div class="dots"><span></span><span></span><span></span><span></span></div>
  <svg class="abs" style="left:0;top:590px" width="1200" height="52" viewBox="0 0 1200 52"><polygon points="0,52 1200,0 1200,52" fill="#fff"/></svg>
</section>

<section class="welcome">
  <div class="brand"><span class="brand-mark"></span>Vaultmerrow</div>
  <h2 class="section-title">Welcome to our website</h2>
  <p class="welcome-text">Aliquam molestie, mi et imperdiet euismod, dui purus auctor tellus, et interdum lacus lectus et ante. Sed accumsan sollicitudin sapien, sit amet adipiscing turpis gravida ac. In congue, neque ac lobortis volutpat, libero mauris varius mi, vitae suscipit ipsum ligula vitae risus.</p>
  <span class="btn">Read More</span>
</section>

<section class="band" style="top:1121px">
  <div class="band-photo" role="img" aria-label="Photo of a person working on a tablet and laptop" style="background:linear-gradient(120deg,#1b2230 0%,#3a4658 45%,#212a38 100%)"></div>
  <svg class="abs" style="left:0;top:0" width="1200" height="445" viewBox="0 0 1200 445">
    <polygon points="0,0 1200,0 1200,10 0,40" fill="#fff"/>
    <polygon points="0,0 700,0 0,38" fill="var(--red)"/>
    <polygon points="1200,445 0,445 1200,400" fill="#fff"/>
    <polygon points="1200,400 1200,445 500,445" fill="var(--red)"/>
  </svg>
  <p class="band-text">LOREM IPSUM DOLOR SIT AMET, CONSECTETUR ADIPISCING<br>NULLA VEL TORTOR ACCUMSAN</p>
</section>

<section class="services">
  <h2 class="section-title">Our Services</h2>
  <p class="intro">Aliquam molestie, mi et imperdiet euismod, dui purus auctor tellus, et interdum lacus lectus et ante. Sed accumsan sollicitudin sapien, sit amet adipiscing turpis gravida ac.</p>

  <div class="vline" style="left:421px;top:1775px;height:680px"></div>
  <div class="vline" style="left:780px;top:1775px;height:680px"></div>
  <div class="hline" style="left:76px;top:2116px;width:320px"></div>
  <div class="hline" style="left:440px;top:2116px;width:320px"></div>
  <div class="hline" style="left:800px;top:2116px;width:324px"></div>

  <div class="service" style="left:76px;top:1820px">
    <svg width="70" height="70" viewBox="0 0 70 70" fill="none" stroke="#555" stroke-width="2"><circle cx="26" cy="40" r="12"/><circle cx="26" cy="40" r="4"/><circle cx="48" cy="22" r="8"/><circle cx="48" cy="22" r="3"/><path d="M26 24v4M26 52v4M10 40h4M38 40h4M48 10v4M48 30v4M36 22h4M56 22h4"/></svg>
    <h3>Risk Management</h3>
    <p>Aliquam molestie, mi et imperdiet euismod, dui purus auctor tellus, et interdum lacus lectus et antes ed accumsan sollicitudin..</p>
  </div>
  <div class="service" style="left:436px;top:1820px">
    <svg width="70" height="70" viewBox="0 0 70 70" fill="none" stroke="#555" stroke-width="2"><rect x="20" y="32" width="30" height="26" rx="2"/><path d="M26 32v-8a9 9 0 0 1 18 0v8"/></svg>
    <h3>Cyber Security</h3>
    <p>Aliquam molestie, mi et imperdiet euismod, dui purus auctor tellus, et interdum lacus lectus et antes ed accumsan sollicitudin..</p>
  </div>
  <div class="service" style="left:794px;top:1820px">
    <svg width="70" height="70" viewBox="0 0 70 70" fill="none" stroke="#555" stroke-width="2"><path d="M20 10h22l10 10v40H20z"/><path d="M42 10v10h10M27 30h18M27 38h18M27 46h18"/></svg>
    <h3>Information Security</h3>
    <p>Aliquam molestie, mi et imperdiet euismod, dui purus auctor tellus, et interdum lacus lectus et antes ed accumsan sollicitudin..</p>
  </div>

  <div class="service" style="left:76px;top:2166px">
    <svg width="70" height="70" viewBox="0 0 70 70" fill="none" stroke="#555" stroke-width="2"><path d="M18 32a17 17 0 0 1 30-10M52 38a17 17 0 0 1-30 10"/><path d="M48 12v10h-10M22 58v-10h10"/></svg>
    <h3>Disaster Recovery</h3>
    <p>Aliquam molestie, mi et imperdiet euismod, dui purus auctor tellus, et interdum lacus lectus et antes ed accumsan sollicitudin..</p>
  </div>
  <div class="service" style="left:436px;top:2166px">
    <svg width="70" height="70" viewBox="0 0 70 70" fill="none" stroke="#555" stroke-width="2"><circle cx="35" cy="35" r="22"/><ellipse cx="35" cy="35" rx="10" ry="22"/><path d="M13 35h44M17 24h36M17 46h36"/></svg>
    <h3>Compliance Management</h3>
    <p>Aliquam molestie, mi et imperdiet euismod, dui purus auctor tellus, et interdum lacus lectus et antes ed accumsan sollicitudin..</p>
  </div>
  <div class="service" style="left:794px;top:2166px">
    <svg width="70" height="70" viewBox="0 0 70 70" fill="none" stroke="#555" stroke-width="2"><ellipse cx="35" cy="16" rx="16" ry="6"/><path d="M19 16v38c0 3 7 6 16 6s16-3 16-6V16M19 29c0 3 7 6 16 6s16-3 16-6M19 42c0 3 7 6 16 6s16-3 16-6"/></svg>
    <h3>Data Security</h3>
    <p>Aliquam molestie, mi et imperdiet euismod, dui purus auctor tellus, et interdum lacus lectus et antes ed accumsan sollicitudin..</p>
  </div>

  <span class="btn">View All Services</span>
</section>

<section class="band" style="top:2621px">
  <div class="band-photo" role="img" aria-label="Photo of a hand touching a glowing digital security interface" style="background:radial-gradient(ellipse at 75% 45%,#c07a3a 0%,#3a3530 25%,#141a22 60%,#0d1118 100%)"></div>
  <svg class="abs" style="left:0;top:0" width="1200" height="445" viewBox="0 0 1200 445">
    <polygon points="0,0 1200,0 1200,10 0,40" fill="#fff"/>
    <polygon points="0,0 700,0 0,38" fill="var(--red)"/>
    <polygon points="1200,445 0,445 1200,400" fill="#fff"/>
    <polygon points="1200,400 1200,445 500,445" fill="var(--red)"/>
  </svg>
  <p class="band-text" style="top:192px">LOREM IPSUM DOLOR SIT AMET, CONSECTETUR ADIPISCING<br>NULLA VEL TORTOR ACCUMSAN</p>
</section>

<section class="resources">
  <div class="res-photo" role="img" aria-label="Photo of hands reviewing printed charts with a pen"></div>
  <h2 class="section-title">Resources</h2>
  <p style="top:3170px">Aliquam molestie, mi et imperdiet euismod, dui purus auctor tellus, et interdum lacus lectus et ante. Sed accumsan sollicitudin sapien, sit amet adipiscing turpis gravida ac. In congue, neque ac lobortis volutpat, libero mauris varius mi, vitae suscipit ipsum ligula vitae risus.</p>
  <p style="top:3302px">Aliquam molestie, mi et imperdiet euismod, dui purus auctor tellus, et interdum lacus lectus et ante. Sed accumsan sollicitudin sapien, sit amet adipiscing, Nam et vestibulum velit. Cras hendrerit felis eu est dapibus pellentesque...</p>
  <span class="btn">View Resources</span>
</section>

<section class="blog">
  <div class="blog-bg"></div>
  <h2 class="section-title">Blog</h2>
  <article class="post" style="left:76px">
    <div class="post-photo" role="img" aria-label="Photo of a team discussing charts on a computer screen" style="background:linear-gradient(135deg,#7d8791 0%,#d8dadc 50%,#8e8a84 100%)"></div>
    <h3>Aliquam molestie, mi et imperdiet euismod</h3>
    <p>Dui purus auctor tellus, et interdum lacus lectus et antesed accumsan sollicitudin sapien, sit amet adipiscing turpis gravida ac egestas risus in magna varius commodo.. <span>Continue Reading</span></p>
  </article>
  <article class="post" style="left:613px">
    <div class="post-photo" role="img" aria-label="Photo of a hand touching a compliance icon interface" style="background:linear-gradient(135deg,#1d6fa8 0%,#4fa3c9 50%,#d38a3a 100%)"></div>
    <h3>Aliquam molestie, mi et imperdiet euismod</h3>
    <p>Dui purus auctor tellus, et interdum lacus lectus et antesed accumsan sollicitudin sapien, sit amet adipiscing turpis gravida ac egestas risus in magna varius commodo.. <span>Continue Reading</span></p>
  </article>
  <span class="btn">View All Posts</span>
  <svg class="abs" style="left:0;top:4225px" width="1200" height="33" viewBox="0 0 1200 33"><polygon points="0,33 1200,0 1200,33" fill="var(--red)"/><polygon points="0,33 1200,12 1200,33" fill="var(--footer)"/></svg>
</section>

<footer class="site-footer">
  <div class="fcol" style="left:76px">
    <h4>Site Map</h4>
    <div>Home</div><div>About Us</div><div>Services</div><div>Resources</div><div>Blog</div><div>Contact Us</div>
  </div>
  <div class="fcol" style="left:253px">
    <h4>Services</h4>
    <div>Compliance Managers</div><div>Risk Managers</div><div>Information Security &amp; Cyber Security Professionals</div><div>Chief Data/Digital Officers</div><div>Chief Operating/Financial Officers</div><div>Business Continuity Professionals</div><div>Disaster Recovery Planners</div><div>Small Business Owners</div>
  </div>
  <div class="fcol" style="left:635px">
    <h4>Contact Info</h4>
    <div style="line-height:22px;padding:3px 0">412 Tallow Lane,<br>Brisbane, QLD 4000</div>
    <div class="row"><svg width="12" height="12" viewBox="0 0 12 12"><path d="M2 1l3 1-1 2 4 4 2-1 1 3-2 1C5 11 1 7 1 3z" fill="#ddd"/></svg>1-800-555-0148</div>
    <div class="row"><svg width="12" height="10" viewBox="0 0 12 10"><rect width="12" height="10" fill="#ddd"/><path d="M0 0l6 5 6-5" stroke="#111" fill="none"/></svg>hello@vaultmerrow.com.au</div>
    <div class="row"><svg width="12" height="14" viewBox="0 0 12 14"><path d="M6 14S0 7 0 6a6 6 0 0 1 12 0c0 1-6 8-6 8z" fill="#ddd"/><circle cx="6" cy="6" r="2" fill="#111"/></svg>Map Location</div>
    <h4 style="margin-top:16px">Connect Us</h4>
    <div class="socials"><span></span><span></span><span></span><span></span><span></span></div>
  </div>
  <div class="fcol" style="left:884px">
    <h4>Email Subscribe</h4>
    <div class="email-field">Enter Email Address</div>
    <span class="btn" style="left:150px;top:104px;width:90px">Sign Up</span>
  </div>
  <div class="chat"><svg width="18" height="16" viewBox="0 0 18 16"><path d="M2 1h14a1 1 0 0 1 1 1v9a1 1 0 0 1-1 1H7l-4 3v-3H2a1 1 0 0 1-1-1V2a1 1 0 0 1 1-1z" fill="var(--red)"/></svg>LIVE CHAT</div>
  <div class="copyright">Copyright © 2019. Vaultmerrow. All Rights Reserved</div>
</footer>

</body>
</html>
```